Business Card Design for Software Development Company

I am looking for a business card design the incorporates my new logo (attached below).

Key information to include:
Name: Martin Quelbrook
Title: CEO
Email: martin@brightwellcivic.example
Phone: 555-218-9403
Website: www.brightwellcivic.example

NOTE: This design should be easy to edit so that we can order cards for different members of our team.

```html
<!DOCTYPE html>
<html lang="en">
<head>
<meta charset="utf-8">
<title>BrightwellLabs Business Card</title>
<link href="https://fonts.googleapis.com/css2?family=Montserrat:wght@400;500;700&display=swap" rel="stylesheet">
<style>
  :root {
    --page: #1c1c1c;
    --card: #272727;
    --ink: #ffffff;
    --muted: #e6e6e6;
    --teal: #16b3a0;
    --orange: #f08a24;
    --orange-deep: #d9531f;
    --peach: #f7cfa0;
    --maroon: #5a1416;
  }
  * { box-sizing: border-box; margin: 0; padding: 0; }
  html, body { width: 1200px; height: 801px; overflow: hidden; }
  body {
    background: var(--page);
    font-family: "Montserrat", sans-serif;
    color: var(--ink);
    position: relative;
  }
  .card {
    position: absolute;
    top: 258px;
    width: 500px;
    height: 286px;
    background: var(--card);
    border-radius: 18px;
    overflow: hidden;
  }
  .card--front { left: 70px; }
  .card--back { left: 630px; }

  /* front */
  .front-artwork {
    position: absolute;
    right: 0; top: 0;
    width: 190px; height: 112px;
    background: linear-gradient(135deg, rgba(22,110,100,0.28) 0%, rgba(110,60,35,0.32) 100%);
  }
  .wordmark {
    display: flex;
    align-items: center;
    gap: 8px;
  }
  .wordmark__dot { width: 12px; height: 12px; background: var(--orange); border-radius: 50%; flex: none; }
  .wordmark__name { font-weight: 700; letter-spacing: -0.5px; white-space: nowrap; }
  .wordmark__tagline {
    font-size: 6px;
    font-weight: 500;
    letter-spacing: 0.6px;
    text-transform: uppercase;
    text-align: right;
    white-space: nowrap;
  }
  .front-brand { position: absolute; left: 36px; top: 40px; }
  .front-brand .wordmark__name { font-size: 28px; }
  .front-brand .wordmark__tagline { margin-top: 2px; }

  .person { position: absolute; left: 60px; top: 128px; }
  .person__name { font-size: 19px; font-weight: 700; letter-spacing: 1.2px; text-transform: uppercase; white-space: nowrap; }
  .person__first { color: var(--teal); }
  .person__last { color: var(--orange); }
  .person__title { font-size: 12px; color: var(--muted); letter-spacing: 1px; margin-top: 2px; }
  .tab { position: absolute; left: 0; top: 132px; width: 38px; height: 24px; background: var(--teal); }

  .contact { position: absolute; left: 60px; top: 192px; list-style: none; }
  .contact li { display: flex; align-items: center; gap: 9px; font-size: 12.5px; color: var(--muted); margin-bottom: 7px; white-space: nowrap; }
  .contact svg { width: 12px; height: 12px; fill: var(--orange); flex: none; }

  /* back */
  .back-artwork {
    position: absolute;
    left: 0; top: 0;
    width: 170px; height: 286px;
    background: linear-gradient(180deg, var(--maroon) 0%, var(--orange-deep) 35%, var(--orange) 65%, var(--peach) 100%);
  }
  .back-brand { position: absolute; right: 30px; bottom: 62px; }
  .back-brand .wordmark__name { font-size: 34px; }
  .back-brand .wordmark__dot { width: 13px; height: 13px; }
  .back-brand .wordmark__tagline { font-size: 7px; margin-top: 3px; }
</style>
</head>
<body>

<section class="card card--front" aria-label="Card front">
  <div class="front-artwork" role="img" aria-label="Faint teal and brown brand artwork"></div>

  <div class="front-brand">
    <div class="wordmark">
      <span class="wordmark__dot"></span>
      <span class="wordmark__name">BrightwellLabs</span>
    </div>
    <p class="wordmark__tagline">A division of Brightwell Civic</p>
  </div>

  <div class="tab"></div>
  <div class="person">
    <p class="person__name"><span class="person__first">Martin</span> <span class="person__last">Quelbrook</span></p>
    <p class="person__title">CEO</p>
  </div>

  <ul class="contact">
    <li>
      <svg viewBox="0 0 24 24" aria-hidden="true"><path d="M6.6 10.8a15.1 15.1 0 0 0 6.6 6.6l2.2-2.2a1 1 0 0 1 1-.25 11.4 11.4 0 0 0 3.6.57 1 1 0 0 1 1 1V20a1 1 0 0 1-1 1A17 17 0 0 1 3 4a1 1 0 0 1 1-1h3.5a1 1 0 0 1 1 1c0 1.25.2 2.45.57 3.6a1 1 0 0 1-.25 1z"/></svg>
      555-218-9403
    </li>
    <li>
      <svg viewBox="0 0 24 24" aria-hidden="true"><path d="M2 5h20v14H2zM4 7v.5l8 5 8-5V7l-8 5z"/></svg>
      martin@brightwellcivic.example
    </li>
    <li>
      <svg viewBox="0 0 24 24" aria-hidden="true"><circle cx="12" cy="12" r="10"/></svg>
      www.brightwellcivic.example
    </li>
  </ul>
</section>

<section class="card card--back" aria-label="Card back">
  <div class="back-artwork" role="img" aria-label="Orange, red and peach brand artwork"></div>
  <div class="back-brand">
    <div class="wordmark">
      <span class="wordmark__dot"></span>
      <span class="wordmark__name">BrightwellLabs</span>
    </div>
    <p class="wordmark__tagline">A division of Brightwell Civic</p>
  </div>
</section>

</body>
</html>
```